Create a banner for me that embodies my health and well being package.

I am an intuitive counselor with a busy practice helping clients to shift their blocks and move forward in their lives.
I have created a package called '9 paths home again'
I am wanting a banner to put on my website page, facebook page and to use as a letter head in mailouts.
My ideal clients are those who want to create change in their lives and who invest money in themselves and their personal and spiritual growth.
I am different to regular life coaches as my sessions have a spiritual twist to them creating much deeper change in my clients.
I would like the banner to be mainly font with the title of the progam: 9 Paths Home Again (no other wording) (something along the lines of the Blackjack font) and that ties in with the theme of my website. I'm not sure what else I want with it and am looking for ideas.
Website:
www.lumorawellspring.com.au
I also have a current facebook page for the business:
https://www.facebook.com/Lumora-Wellspring-Studio-502718364091557/
(Note: I am about to drop my logo and business name and move to using my own name - the rest of the website will remain the same).
I have attached a doc with the draft of what wording will be on the website page any advertising will link to, to give you an idea of what the program is about.

Target Market(s)

People who invest money on themselves who are looking to improve their emotional well being and creating change in their life. Majority are middle aged women (also younger females and some men)

Industry/Entity Type

Health And Wellness

Font styles to use
Other font styles liked:
• I like Blackjack and Amienne. Along those lines.

Requirements
Must have
• Attractive, modern and GREAT font.
Nice to have
• Surprise me with something amazing!
• I love the colours in the 2 images I have up loaded as they represent the heart chakra colours. They could be a feature on the banner or blurred into the background.
Should not have
• Even though my work is quite spiritual I don't want it to look woo woo (meaning airy fairy spiritual stuff!)

```html
<!DOCTYPE html>
<html lang="en">
<head>
<meta charset="utf-8">
<title>9 Paths Home Again</title>
<link rel="stylesheet" href="https://fonts.googleapis.com/css2?family=Dancing+Script:wght@600&display=swap">
<style>
  :root {
    --bloom-deep: #1a2670;
    --bloom-mid: #3348b8;
    --bloom-light: #5a72dc;
    --bloom-shadow: #0f1850;
    --title-ink: #ffffff;
  }
  html, body {
    margin: 0;
    padding: 0;
    width: 1200px;
    height: 545px;
    overflow: hidden;
    background: var(--bloom-deep);
  }
  .banner {
    position: relative;
    width: 1200px;
    height: 545px;
    overflow: hidden;
  }
  .flower-field {
    position: absolute;
    inset: 0;
    background:
      radial-gradient(ellipse 40% 35% at 20% 30%, rgba(90,114,220,0.55), transparent 70%),
      radial-gradient(ellipse 35% 30% at 75% 20%, rgba(90,114,220,0.5), transparent 70%),
      radial-gradient(ellipse 45% 35% at 55% 75%, rgba(90,114,220,0.5), transparent 70%),
      radial-gradient(ellipse 30% 30% at 10% 85%, rgba(15,24,80,0.5), transparent 70%),
      radial-gradient(ellipse 30% 30% at 92% 70%, rgba(15,24,80,0.45), transparent 70%),
      linear-gradient(160deg, var(--bloom-mid) 0%, var(--bloom-deep) 55%, var(--bloom-mid) 100%);
  }
  .program-title {
    position: absolute;
    left: 0;
    right: 0;
    top: 190px;
    margin: 0;
    text-align: center;
    font-family: "Dancing Script", cursive;
    font-weight: 600;
    font-size: 52px;
    line-height: 1.2;
    color: var(--title-ink);
    text-shadow: 0 0 3px var(--bloom-shadow), 1px 1px 2px var(--bloom-shadow);
    white-space: nowrap;
  }
</style>
</head>
<body>
  <div class="banner">
    <div class="flower-field" role="img" aria-label="A dense carpet of small blue five-petalled flowers filling the whole banner"></div>
    <h1 class="program-title">9 paths home again</h1>
  </div>
</body>
</html>
```